Brand New Product Needs Sales Focused Website Design

Looking for design of Homepage, Category Page & Product Page for single product sales focused website. TrundleCrate manufacture and distribute a brand new product to the market called PalTote-Case which is a super strong, re-useable, folding & stacking plastic box which can be seen on our current website www.paltote-case.example PalTote-Case was originally developed as an alternative to supermarket carrier bags and was pitched as a box for life against the other low end re-useable products. The original version was made from recycled plastic and pitched very much as environmental product. We are now taking a different direction and have re-designed the boxes in 5 bright and fashionable designs and although we still want the primary focus to be supermarket shopping we want to position the product as a design led, must have shopping and household accessory rather than a boring, cheap looking black plastic box. The new designs will still have the environmental benefits of being able to be re-used thousands of times and being 100% recyclable and save on the imminent 5p tax on carrier bags in the UK however the new designs will not be made from recycled material. Although the main use for PalTote-Case is supermarket shopping it has a multitude of other uses especially where you need temporary storage - laundry, back of the car, moving house/students, gardening, days out, home office filing (will take A4 file), recycling and much more - PalTote-Case is made out of super strong Polypropylene and can be easily washed and sanitised after use and can be folded and unfolded thousands of times and so will last for many years. PalTote-Case is a product that needs to be seen in action to be understood so the web design must quickly and easily communicate what PalTote-Case is and how it works - this can be done with video, images and copy. Our current website does not work for many reasons:- it is too busy, has too much information, tries too hard and ultimately isn't working. Any of the images off our current website can be supplied for use. Once the concept of the website is agreed I can get these photoshopped with the new designs. Pictures of new designs for reference will be attached to this brief. Ultimately we want the website to convert visitors to sales and therefore designers with a proven track record in this field are especially welcome to enter. We also have a Dropbox folder with over 100 product and situation images in - please send email address and we will send an invite to the folder. Due to Christmas period this competition will be run over 15 days however we may choose to extend the deadline to account for the non working days. Any questions feel free to ask - we will respond within 24 hours where possible.

```html
<!DOCTYPE html>
<html lang="en">
<head>
<meta charset="utf-8">
<title>PalTote-Case – Home</title>
<link href="https://fonts.googleapis.com/css2?family=Open+Sans:wght@400;600&family=Roboto:wght@400;500;700&family=Tinos&display=swap" rel="stylesheet">
<style>
:root{
  --ink:#333;
  --muted:#888;
  --line:#e2e2e2;
  --blue:#2a5d9a;
  --link:#2f5c8f;
  --pink:#e0457b;
  --price-old:#e4585a;
  --price-new:#6f8fd0;
  --dark:#1c1c1c;
  --footer:#f3f3f3;
  --bottom:#e6e6e6;
  --card:#e9e9e9;
}
*{box-sizing:border-box;margin:0;padding:0}
html,body{width:720px;height:1200px;overflow:hidden;background:#fff}
body{position:relative;font-family:"Open Sans",sans-serif;color:var(--ink)}
.abs{position:absolute}

/* top bar */
.topbar{left:0;top:0;width:720px;height:36px;border-bottom:1px solid var(--line)}
.account{left:66px;top:12px;font:8px "Open Sans",sans-serif;color:var(--muted);white-space:nowrap}
.account a{color:var(--link);text-decoration:none}
.search{left:502px;top:6px;width:152px;height:24px;border:1px solid var(--line);border-radius:12px;font:8px "Open Sans",sans-serif;color:#c4c4c4;padding:7px 0 0 7px}
.search-btn{position:absolute;right:0;top:-1px;width:24px;height:24px;border-left:1px solid var(--line)}

/* header */
.brand{left:66px;top:44px;font:600 25px/30px "Open Sans",sans-serif;color:var(--pink);letter-spacing:-.5px;white-space:nowrap}
.tagline{left:74px;top:81px;font:500 10.5px Roboto,sans-serif;color:#111;letter-spacing:.2px;white-space:nowrap}
.nav{left:297px;top:64px;display:flex;gap:19px;font:400 8.3px Roboto,sans-serif;color:var(--muted);text-transform:uppercase;white-space:nowrap}
.nav .active{color:var(--pink)}

/* hero */
.hero{left:0;top:101px;width:720px;height:349px;background:linear-gradient(180deg,#e3d8c3 0%,#d8ccb3 35%,#c9c9c8 55%,#b08a6e 80%,#9c6d52 100%)}
.hero-title{left:66px;top:234px;height:32px;padding:0 6px;background:rgba(20,20,20,.82);font:700 23px/32px Roboto,sans-serif;color:#fff;letter-spacing:-.4px;white-space:nowrap}
.hero-sub{left:66px;top:266px;height:28px;padding:0 6px;background:rgba(20,20,20,.72);font:500 16px/28px Roboto,sans-serif;color:#fff;white-space:nowrap}
.hero-cta{left:66px;top:296px;width:69px;height:22px;background:var(--blue);font:500 8.5px/22px Roboto,sans-serif;color:#fff;text-align:center}
.arrow{top:254px;width:30px;height:44px;background:rgba(70,70,70,.75)}
.dots{left:344px;top:436px;display:flex;gap:4px}
.dots span{width:6px;height:6px;border-radius:50%;background:rgba(80,80,80,.6)}
.dots span:first-child{background:#6fb33e}

/* usage strip */
.use{top:470px;width:142px}
.use .shot{height:96px;border:3px solid #e5e5e5}
.use .label{margin-top:7px;font:600 10px "Open Sans",sans-serif;color:#444;padding-bottom:7px;border-bottom:2px solid var(--line);white-space:nowrap}

/* sidebar */
.side{left:66px;top:606px;width:142px}
.side-head{height:25px;background:#f1f1f1;border-bottom:2px solid #e3e3e3;font:500 10px Roboto,sans-serif;padding:7px 6px 0;text-transform:uppercase}
.side-item{height:24.6px;border-bottom:1px solid var(--line);font:8.3px "Open Sans",sans-serif;color:#666;padding:6px 6px 0;display:flex;justify-content:space-between;white-space:nowrap}
.side-item.first{color:#333;font-weight:600}
.promo{left:66px;top:843px;width:142px;height:159px;border:3px solid #e0e0e0;background:#fff}

/* featured */
.feat-title{left:214px;top:609px;font:500 10px Roboto,sans-serif;text-transform:uppercase;white-space:nowrap}
.feat-rule{left:214px;top:629px;width:440px;height:1px;background:var(--line)}
.feat-rule::before{content:"";position:absolute;left:0;top:-1px;width:44px;height:2px;background:#d6d6d6}
.ship{left:214px;top:638px;width:440px;height:32px;background:var(--dark);padding:2px}
.ship-inner{height:100%;border:1px solid #555;text-align:center;font-family:Tinos,serif;color:#fff}
.ship-inner b{display:block;font-weight:400;font-size:10.5px;padding-top:3px}
.ship-inner small{display:block;font-size:6.5px;color:#999}

.card{width:142px;height:158px;background:#f2f2f2;border:3px solid var(--card)}
.card .pic{height:98px;position:relative}
.card .name{margin:14px 0 0 5px;font:400 11px "Open Sans",sans-serif;color:#333;white-space:nowrap}
.card .price{margin:5px 0 0 5px;font:8.7px "Open Sans",sans-serif;white-space:nowrap}
.card .old{color:var(--price-old);text-decoration:line-through;margin-right:12px}
.card .new{color:var(--price-new)}
.hover-btn{position:absolute;top:42px;width:21px;height:20px;background:#fff}

/* footer */
.footer{left:0;top:1026px;width:720px;height:138px;background:var(--footer)}
.fcol{top:1036px;width:142px}
.fcol h4{font:500 9px Roboto,sans-serif;text-transform:uppercase;padding-bottom:7px;border-bottom:1px solid #ddd;white-space:nowrap}
.fcol p,.fcol li{font:7.6px/12px "Open Sans",sans-serif;color:#999;list-style:none}
.fcol .gap{margin-top:10px}
.fcol .narrow{width:124px}
.social{display:flex;gap:10px;margin-top:9px}
.social span{width:10px;height:10px;border-radius:50%;background:#bdbdbd}
.mail{top:1070px;left:511px;width:91px;height:20px;border:1px solid #ddd;background:#fff;font:7.6px "Open Sans",sans-serif;color:#999;padding:5px 6px;white-space:nowrap}
.mail-btn{top:1070px;left:602px;width:52px;height:20px;background:var(--blue);font:600 7.8px/20px "Open Sans",sans-serif;color:#fff;text-align:center}
.bottom{left:0;top:1164px;width:720px;height:36px;background:var(--bottom)}
.copy{left:66px;top:1176px;font:7.8px "Open Sans",sans-serif;color:#888;white-space:nowrap}
.pay{left:534px;top:1176px;display:flex;gap:4px}
.pay span{width:20px;height:13px;border-radius:2px;background:#fff;border:1px solid #ccc}
</style>
</head>
<body>

<header>
  <div class="abs topbar"></div>
  <div class="abs account">
    <svg width="7" height="7" viewBox="0 0 10 10"><path d="M1 4h5V2l3 3-3 3V6H1z" fill="#2f5c8f"/></svg>
    <a>Sign in</a> or <a>Create an account</a> &nbsp;
    <svg width="8" height="7" viewBox="0 0 12 10"><path d="M0 0h2l1 6h7l2-5H3" fill="none" stroke="#2f5c8f" stroke-width="1.4"/><circle cx="4" cy="9" r="1" fill="#2f5c8f"/><circle cx="9" cy="9" r="1" fill="#2f5c8f"/></svg>
    <a>(0) items in cart | ($0.00)</a>
  </div>
  <div class="abs search">Type here to Search
    <div class="search-btn"><svg width="24" height="24" viewBox="0 0 24 24"><circle cx="11" cy="11" r="2.6" fill="none" stroke="#444" stroke-width="1.3"/><path d="M13 13l2.4 2.4" stroke="#444" stroke-width="1.4"/></svg></div>
  </div>

  <div class="abs brand">PalTote-Case</div>
  <div class="abs tagline">INGENENIOUS &amp; PRACTICAL</div>
  <nav class="abs nav">
    <span class="active">Home</span><span>Catagory</span><span>Our Range</span><span>Gaurantee</span><span>Products</span><span>Contact Us</span>
  </nav>
</header>

<section>
  <div class="abs hero" role="img" aria-label="Shopper beside a silver car with its boot open, two blue folding crates full of groceries inside, on a brick driveway"></div>
  <div class="abs hero-title">SHOPPING MADE EASY</div>
  <div class="abs hero-sub">With PalTote-Case</div>
  <div class="abs hero-cta">VIEW ALL</div>
  <div class="abs arrow" style="left:0"><svg width="30" height="44"><path d="M19 12l-8 10 8 10" fill="none" stroke="#fff" stroke-width="1.5"/></svg></div>
  <div class="abs arrow" style="left:690px"><svg width="30" height="44"><path d="M11 12l8 10-8 10" fill="none" stroke="#fff" stroke-width="1.5"/></svg></div>
  <div class="abs dots"><span></span><span></span><span></span><span></span></div>
</section>

<section>
  <div class="abs use" style="left:66px"><div class="shot" role="img" aria-label="Blue crates in a trolley at a supermarket checkout" style="background:linear-gradient(180deg,#9aa1a5,#d9dbdc 55%,#3f63b8)"></div><div class="label">PalTote-Case</div></div>
  <div class="abs use" style="left:214px"><div class="shot" role="img" aria-label="Filled blue crates being lifted into a car boot" style="background:linear-gradient(180deg,#d8d2c2,#7d7e82 50%,#3a5fb8)"></div><div class="label">PalTote-Case</div></div>
  <div class="abs use" style="left:363px"><div class="shot" role="img" aria-label="Crate being packed at a green self-service checkout" style="background:linear-gradient(180deg,#3b3b40,#5fae4c 50%,#2f55a8)"></div><div class="label">PalTote-Case</div></div>
  <div class="abs use" style="left:512px"><div class="shot" role="img" aria-label="Two filled blue crates on a kitchen counter" style="background:linear-gradient(180deg,#ece6d6,#d2cbb8 45%,#2e55b0)"></div><div class="label">PalTote-Case</div></div>
</section>

<aside class="abs side">
  <div class="side-head">Catagory</div>
  <div class="side-item first">Lorem Ipsum Dolor <svg width="8" height="8"><path d="M1 2l3 3 3-3" fill="none" stroke="#555" stroke-width="1.2"/></svg></div>
  <div class="side-item">Sit Amet Consectetur</div>
  <div class="side-item">Adipiscing Elit</div>
  <div class="side-item">Sed Do Euismod</div>
  <div class="side-item">Tempor Incidunt</div>
  <div class="side-item">Ut Labore</div>
  <div class="side-item">Et Dolore</div>
  <div class="side-item">Magna Aliqua</div>
</aside>
<div class="abs promo" role="img" aria-label="The range of four crate designs: leather satchel, brown folder, wooden crate and a filled wooden crate" style="background:linear-gradient(180deg,#ffffff 20%,#e6d3c0 55%,#9a6a44)"></div>

<main>
  <div class="abs feat-title">Featured Products</div>
  <div class="abs feat-rule"></div>
  <div class="abs ship"><div class="ship-inner"><b>FREE SHIPPING</b><small>Not on International Shipping</small></div></div>

  <div class="abs card" style="left:214px;top:677px"><div class="pic" role="img" aria-label="Open white folding crate" style="background:linear-gradient(180deg,#f4f4f4,#c3c6ca 60%,#6c6f72)"></div><div class="name">PalTote-Case</div><div class="price"><span class="old">$50.00</span><span class="new">$45.00</span></div></div>
  <div class="abs card" style="left:363px;top:677px"><div class="pic" role="img" aria-label="Blue folding crate" style="background:linear-gradient(180deg,#2b5fb8,#1f4d9e)">
      <div class="hover-btn" style="left:42px"><svg width="21" height="20" viewBox="0 0 21 20"><path d="M6 7h1l1 5h5l1-4H7.5" fill="none" stroke="#1f4d9e" stroke-width="1.3"/></svg></div>
      <div class="hover-btn" style="left:73px"><svg width="21" height="20" viewBox="0 0 21 20"><ellipse cx="10.5" cy="10" rx="4.5" ry="2.8" fill="none" stroke="#1f4d9e" stroke-width="1.2"/><circle cx="10.5" cy="10" r="1.3" fill="#1f4d9e"/></svg></div>
    </div><div class="name">PalTote-Case</div><div class="price"><span class="old">$50.00</span><span class="new">$45.00</span></div></div>
  <div class="abs card" style="left:512px;top:677px"><div class="pic" role="img" aria-label="Wood-effect folding crate" style="background:linear-gradient(180deg,#e8e8e8 6%,#8a5a34 28%,#6b4327 82%,#3a3a3a)"></div><div class="name">PalTote-Case</div><div class="price"><span class="old">$50.00</span><span class="new">$45.00</span></div></div>

  <div class="abs card" style="left:214px;top:843px"><div class="pic" role="img" aria-label="Brown leather satchel design crate" style="background:linear-gradient(180deg,#27384a,#9b5a34 25%,#7a3f22 88%,#27384a)"></div><div class="name">PalTote-Case</div><div class="price"><span class="old">$50.00</span><span class="new">$45.00</span></div></div>
  <div class="abs card" style="left:363px;top:843px"><div class="pic" role="img" aria-label="Light blue satchel design crate" style="background:linear-gradient(180deg,#27384a,#5d8fc8 25%,#4a7bb5 88%,#27384a)"></div><div class="name">PalTote-Case</div><div class="price"><span class="old">$50.00</span><span class="new">$45.00</span></div></div>
  <div class="abs card" style="left:512px;top:843px"><div class="pic" role="img" aria-label="Wicker basket design crate" style="background:linear-gradient(180deg,#27384a,#8c7a66 25%,#b49f86 75%,#27384a)"></div><div class="name">PalTote-Case</div><div class="price"><span class="old">$50.00</span><span class="new">$45.00</span></div></div>
</main>

<footer>
  <div class="abs footer"></div>
  <div class="abs fcol" style="left:66px"><h4>Text Widget</h4>
    <p class="gap narrow">Lorem ipsum dolor sit amet, con-sectetur adipiscing elit, sed do eiusmod tempor incididunt ut labore et dolore magna aliqua.</p>
    <p class="gap narrow">Ut enim ad minim veniam, quis nostrud exercitation..</p></div>
  <div class="abs fcol" style="left:214px"><h4>Quick Links</h4>
    <ul class="gap"><li>Home</li><li>Catagory</li><li>Our Range</li><li>Gaurantee</li><li>Products</li><li>Contact Us</li></ul></div>
  <div class="abs fcol" style="left:362px"><h4>We Are Social</h4>
    <p class="gap narrow">We are with you in these socia sites. come and join us.</p>
    <div class="social"><span></span><span></span><span></span><span></span></div></div>
  <div class="abs fcol" style="left:511px"><h4>Mailing List</h4></div>
  <div class="abs mail">Your Email Id</div>
  <div class="abs mail-btn">Sign Up</div>

  <div class="abs bottom"></div>
  <div class="abs copy">Copyright © 2014 PalTote-Case | All Rights Reserved</div>
  <div class="abs pay"><span></span><span></span><span></span><span></span><span></span></div>
</footer>

</body>
</html>
```